Design website home page for pathology consulting company

Starting a new consulting company with anatomic pathologists focused on expert diagnosis and second opinions on difficult pathology cases. In the near future we will be incorporating next generation diagnostics for rare diseases of childhood into the business. These include discovery and testing of DNA for mutations.

The company is formed around one of the best known pathologists in the world named Marcel "Biscuit" Trowell. The name of the company is "BiscuitLab"

We had a logo design by SketchForum - it is great. I will attach file as soon as I have it (contest ending today). Our company is medical, uses microscopes, DNA, probably will focus on childhood diseases but not solely on childhood diseases. we're not particularly conservative, but the customers we want to appeal to include older practicing pathologists as well as patients (sometimes parents) looking for second opinions.

Think a group of expert doctors diagnosing disease through the microscope and through DNA technology, ages ranging from 35-75 all trained by the best pathologist in the world - "Biscuit"

We receive glass slides from diseases from patients all over the world from docs who need an expert to tell them what is the diagnosis. So "path to the diagnosis" is also part of the company marketing message.

We want the website design to describe our company but be very simple to find what one is looking for as we will use it as the launch page to:
1) order services
2) check results/reports
3) set up new account
4) speak with one of the pathologists
5) see our test menu
6) access our educational material/webinars
Updates

Update - looking for home page design and then finalists will ask for second page design to keep with theme - ok?

Reason: realized this project isn't web design but web home page design - thanks

Reason: Holidays for some in next two weeks

Reason: Hot discussion among collaborators for a few of the submissions. Will provide detail individually this weekend. Thanks so much for all the submissions!

Target Market(s)

Referring pathologists, physicians who want second opinions on pathology disease diagnosis, patients who have had biopsies (either patients themselves or parents of patients), generally high education level

Industry/Entity Type

Marketing

Requirements
Must have
• BiscuitLab
Next Generation Pathology Consultants

```html
<!DOCTYPE html>
<html lang="en">
<head>
<meta charset="utf-8">
<title>BiscuitLab — Next Generation Pathology Consultants</title>
<link href="https://fonts.googleapis.com/css2?family=Open+Sans:wght@300;400;600;700&family=Roboto:wght@400;500;700&display=swap" rel="stylesheet">
<style>
:root{
  --blue:#0d5aa7;
  --blue-dark:#0a4a8e;
  --blue-deep:#1d4f8a;
  --footer:#2a63a3;
  --footer-bar:#1f5291;
  --navy:#0f3f7a;
  --text:#555;
  --muted:#888;
  --line:#e4e4e4;
  --heading:#333;
}
*{box-sizing:border-box;margin:0;padding:0}
html,body{width:1116px;height:1200px;overflow:hidden;background:#fff}
body{position:relative;font-family:Roboto,Arial,sans-serif;color:var(--text)}
.abs{position:absolute}
a{color:inherit;text-decoration:none}

/* header */
.header-glow{left:0;top:0;width:1116px;height:120px;background:radial-gradient(ellipse at 45% 0%,#f1f1f1 0%,#fff 70%)}
.brand{left:120px;top:10px;width:150px;text-align:center}
.brand-mark{width:70px;height:70px;border-radius:50%;background:#c9cbce;margin:0 auto 4px}
.brand-name{font-family:"Open Sans",sans-serif;font-size:21px;font-weight:400;color:var(--blue);letter-spacing:.5px;line-height:1}
.brand-tag{font-family:"Open Sans",sans-serif;font-size:8px;color:#777;margin-top:3px}
.util{right:112px;top:21px;font-size:12px;color:#555;display:flex;gap:10px}
.util span{display:flex;align-items:center;gap:4px}
.util .sep{width:1px;height:14px;background:#ccc}
.order{right:111px;top:48px;font-size:15px;font-weight:700;color:#222}
.order b{color:var(--blue);font-weight:500;margin-left:4px}
.chat{right:111px;top:77px;font-size:13px;color:#888;display:flex;gap:5px;align-items:center}

/* nav */
.nav{left:102px;top:121px;width:912px;height:33px;background:linear-gradient(#1464b4,#0a4f98);border-radius:3px;display:flex;align-items:center;font-size:12px;color:#fff}
.nav a{padding:0 25px;height:33px;line-height:33px}
.nav a.active{background:var(--navy);border-radius:3px 0 0 3px;padding:0 15px;margin-right:20px}
.nav .search{position:absolute;right:8px;top:5px;width:23px;height:23px;background:#fff;border-radius:2px}

/* hero */
.hero{left:102px;top:160px;width:912px;height:381px;border-radius:3px;overflow:hidden;background:linear-gradient(90deg,#eef2f5 0%,#dde6ec 35%,#c9d6df 55%,#b7a08c 80%,#9a6d52 100%)}
.hero-fade{position:absolute;left:0;top:100px;width:340px;height:190px;background:rgba(255,255,255,.55)}
.hero-copy{left:127px;top:275px;font-family:"Open Sans",sans-serif;color:var(--blue-dark)}
.hero-copy .l1{font-size:37px;font-weight:300;line-height:1;letter-spacing:-1px}
.hero-copy .l2{font-size:51px;font-weight:700;line-height:1;letter-spacing:-1.5px;margin-top:2px}
.hero-copy .l3{font-size:16px;color:#333;margin-top:12px}
.start{left:129px;top:404px;width:117px;height:31px;background:linear-gradient(#2f7cc9,#0f57a2);color:#fff;font-size:19px;font-weight:700;text-align:center;line-height:31px}

/* diagnose bar */
.diag{left:102px;top:547px;width:912px;height:45px;background:linear-gradient(#1a66b5,#0b4f97);border-radius:3px;color:#fff;font-size:14px}
.diag-tab{position:absolute;left:0;top:0;height:45px;width:186px;background:#2c74bf;clip-path:polygon(0 0,170px 0,186px 50%,170px 100%,0 100%);line-height:45px;padding-left:14px;font-size:14px}
.diag-label{position:absolute;top:0;line-height:45px}
.sel{position:absolute;top:11px;height:24px;background:#fff;border-radius:2px;color:#999;font-size:11.5px;line-height:24px;padding-left:12px}
.sel svg{position:absolute;right:10px;top:8px}
.go{position:absolute;right:18px;top:11px;width:27px;height:24px;background:#fff;color:#333;font-size:12px;text-align:center;line-height:24px;border-radius:2px}

/* features */
.features{left:92px;top:614px;width:920px;height:158px;background:#fbfbfb}
.feature{position:absolute;top:626px;width:270px}
.feature h3{display:flex;align-items:center;gap:10px;font-size:16px;font-weight:700;color:var(--blue)}
.ico{width:39px;height:39px;border-radius:50%;background:var(--blue);display:flex;align-items:center;justify-content:center}
.feature p{font-size:14px;line-height:22.5px;color:#555;margin-top:19px}

.rule{left:108px;top:786px;width:904px;height:1px;background:var(--line)}

/* columns */
.col{position:absolute;top:815px;width:205px}
.col h4{font-family:"Open Sans",sans-serif;font-size:13px;font-weight:700;color:var(--heading);display:flex;align-items:center;gap:8px}
.col h4::after{content:"";flex:1;height:9px;background:repeating-linear-gradient(45deg,#e6e6e6 0 1px,#f7f7f7 1px 3px)}
.about p{font-size:11.5px;line-height:18.6px;color:#888;margin-top:12px}
.list{list-style:none;margin-top:16px}
.list li{font-size:11.5px;color:#666;line-height:18.6px;padding:0 0 8px 11px;border-bottom:1px solid #eee;margin-bottom:8px;position:relative}
.list li::before{content:"";position:absolute;left:1px;top:6px;border:3px solid transparent;border-left:3px solid #1a5da6;border-right:0}
.post{display:flex;gap:10px;padding-bottom:9px;border-bottom:1px solid #eee;margin-bottom:10px}
.post .thumb{width:54px;height:50px;border:3px solid #f0f0f0;background:linear-gradient(135deg,#cfe0ea,#9fb7c6)}
.post b{display:block;font-size:11.5px;color:#777;line-height:15px}
.post small{display:block;font-size:10.5px;color:#999;margin-top:4px}

/* footer */
.footer{left:0;top:1042px;width:1116px;height:120px;background:var(--footer)}
.footer-bar{left:0;top:1162px;width:1116px;height:38px;background:var(--footer-bar);color:#fff;font-size:9.5px;text-align:center;line-height:38px;letter-spacing:.2px}
.flinks{position:absolute;top:1066px;font-size:8.5px;color:#fff;line-height:17px;font-weight:500}
.news-h{left:438px;top:1067px;color:#fff;font-size:11px;font-weight:700}
.field{position:absolute;top:1093px;width:160px;height:20px;background:#fff;border:1px solid #ccd;font-size:7.5px;color:#888;line-height:18px;padding-left:10px}
.subscribe{left:664px;top:1125px;width:105px;height:23px;background:linear-gradient(#5c6774,#3f4853);color:#fff;font-size:9px;font-weight:700;text-align:center;line-height:23px;border-radius:2px}
.follow{left:847px;top:1067px;color:#fff;font-size:11px;font-weight:700}
.dot{position:absolute;top:1092px;width:26px;height:26px;border-radius:50%}
</style>
</head>
<body>

<div class="abs header-glow"></div>
<div class="abs brand">
  <div class="brand-mark"></div>
  <div class="brand-name">BiscuitLab</div>
  <div class="brand-tag">Next Generation Pathology Consultants</div>
</div>

<div class="abs util">
  <span><svg width="9" height="11" viewBox="0 0 9 11"><rect x=".5" y=".5" width="8" height="10" fill="none" stroke="#555"/><path d="M2 4h5M2 6h5M2 8h4" stroke="#555"/></svg>Register</span><i class="sep"></i>
  <span><svg width="11" height="11" viewBox="0 0 11 11"><circle cx="5.5" cy="3" r="2.6" fill="#1a5da6"/><path d="M0 11c0-4 11-4 11 0z" fill="#1a5da6"/></svg>Sign In</span><i class="sep"></i>
  <span><svg width="13" height="10" viewBox="0 0 13 10"><path d="M1 3c3-3 8-3 11 0l-2 2-2-1V3H5v1L3 5z" fill="#1a5da6"/><rect x="3" y="6" width="7" height="4" fill="#1a5da6"/></svg>contact</span>
</div>
<div class="abs order">24/7 ORDER <b>080-5550-142</b></div>
<div class="abs chat"><svg width="18" height="15" viewBox="0 0 18 15"><ellipse cx="9" cy="6.5" rx="8" ry="5.5" fill="none" stroke="#999"/><path d="M4 11l-1 3 4-2" fill="none" stroke="#999"/><path d="M5 5h8M5 8h6" stroke="#bbb"/></svg>LIVE CHAT</div>

<nav class="abs nav">
  <a class="active">Home</a><a>About Us</a><a>Services</a><a>Pathology Consultants</a><a>Patients</a><a>Contact Us</a>
  <span class="search"><svg width="23" height="23" viewBox="0 0 23 23"><circle cx="10" cy="10" r="6" fill="none" stroke="#0f4f97" stroke-width="2.4"/><path d="M14.5 14.5l5 5" stroke="#0f4f97" stroke-width="3"/></svg></span>
</nav>

<section class="abs hero" role="img" aria-label="Three pathologists in lab coats examining a sample beside a microscope">
  <div class="hero-fade"></div>
</section>
<div class="abs hero-copy">
  <div class="l1">Focus on Its</div>
  <div class="l2">Precision</div>
  <div class="l3">Now Diagnose your disease online</div>
</div>
<a class="abs start">Start Here</a>

<form class="abs diag">
  <div class="diag-tab">Diagnose Disease Online</div>
  <span class="diag-label" style="left:203px">I am</span>
  <div class="sel" style="left:234px;width:292px">Tell us who are you<svg width="10" height="6" viewBox="0 0 10 6"><path d="M1 1l4 4 4-4" fill="none" stroke="#555" stroke-width="1.5"/></svg></div>
  <span class="diag-label" style="left:521px">Help me</span>
  <div class="sel" style="left:576px;width:277px">--Select--<svg width="10" height="6" viewBox="0 0 10 6"><path d="M1 1l4 4 4-4" fill="none" stroke="#555" stroke-width="1.5"/></svg></div>
  <div class="go">GO</div>
</form>

<div class="abs features"></div>
<div class="feature" style="left:120px">
  <h3><span class="ico"><svg width="18" height="17" viewBox="0 0 18 17"><rect x="1" y="2" width="16" height="14" fill="none" stroke="#fff" stroke-width="1.6"/><rect x="1" y="2" width="16" height="4" fill="#fff"/><path d="M4 9h2M8 9h2M12 9h2M4 12h2M8 12h2M12 12h2" stroke="#fff" stroke-width="1.6"/></svg></span>Check Reports</h3>
  <p>Praesent et ullamcorper erat. Aliquam justo lacus, lobortis eget tempor a, feugiat et ant usce ultrices.</p>
</div>
<div class="feature" style="left:426px">
  <h3><span class="ico"><svg width="20" height="20" viewBox="0 0 20 20"><circle cx="8" cy="12" r="4.5" fill="none" stroke="#fff" stroke-width="2.5" stroke-dasharray="2 1.5"/><circle cx="8" cy="12" r="1.6" fill="#fff"/><circle cx="15" cy="5" r="3" fill="none" stroke="#fff" stroke-width="2" stroke-dasharray="1.5 1"/></svg></span>Order Services</h3>
  <p>Praesent et ullamcorper erat. Aliquam justo lacus, lobortis eget tempor a, feugiat et ant usce ultrices.</p>
</div>
<div class="feature" style="left:735px">
  <h3><span class="ico"><svg width="22" height="16" viewBox="0 0 22 16"><circle cx="6" cy="4" r="3" fill="#fff"/><circle cx="16" cy="4" r="3" fill="#fff"/><path d="M0 14c0-6 12-6 12 0zM10 14c0-6 12-6 12 0z" fill="#fff"/></svg></span>Diagnosis</h3>
  <p>Praesent et ullamcorper erat. Aliquam justo lacus, lobortis eget tempor a, feugiat et ant usce ultrices.</p>
</div>

<div class="abs rule"></div>

<div class="col about" style="left:122px">
  <h4>ABOUT US</h4>
  <p>Lorem ipsum dolor sit amet, consectetur adipisicing elit, sed do eiusmod tempor incididunt ut labore et dolore magna aliqua. Ut enim ad minim veniam, quis nostrud exercitation ullamco laboris nisi ut aliquip ex ea commodo consequat.</p>
</div>
<div class="col" style="left:343px">
  <h4>ACCESS WEBINARS</h4>
  <ul class="list">
    <li>Examination of symptoms using latest technologies</li>
    <li>Ask our doctor a question!</li>
    <li>Health and care?</li>
    <li>Dental Hygienist Career</li>
  </ul>
</div>
<div class="col" style="left:568px">
  <h4>SPEAK WITH PATHOLOGIST</h4>
  <div style="margin-top:16px">
    <div class="post"><div class="thumb" role="img" aria-label="Doctor with patient"></div><div><b>The ultimate cure for patients</b><small>Posted Sept 30, 2012</small></div></div>
    <div class="post"><div class="thumb" role="img" aria-label="Patient at a dental visit"></div><div><b>Dental Hygienist and patient</b><small>Posted Sept 30, 2012</small></div></div>
  </div>
</div>
<div class="col" style="left:788px">
  <h4>TEST MENU</h4>
  <ul class="list" style="margin-top:18px">
    <li>Doctors</li><li>Therapy</li><li>Medical</li><li>Healthcare</li>
  </ul>
</div>

<footer class="abs footer"></footer>
<div class="flinks" style="left:147px">HOME<br>ABOUT US<br>WHY<br>HOW IT WORKS</div>
<div class="flinks" style="left:281px">TESTS &amp; PANELS<br>LAB LOCATIONS<br>CONTACT US<br>LOGIN</div>
<div class="abs news-h">NEWSLETTER SIGNUP</div>
<div class="field" style="left:439px">NAME :</div>
<div class="field" style="left:608px">EMAIL :</div>
<div class="abs subscribe">SUBSCRIBE</div>
<div class="abs follow">FOLLOW US :</div>
<span class="dot" style="left:849px;background:#4aa0d8"></span>
<span class="dot" style="left:880px;background:#e3b42a"></span>
<div class="abs footer-bar">COPYRIGHT © 2013 ALL RIGHTS RESERVED. BISCUITLAB</div>

</body>
</html>
```